Real Estate Office Front Facade Redesign - ideas needed

Kindly read this brief thoroughly as there are 2 deliverables:
1. Office building façade redesign (see attached logo and also photo of our office building façade)
2. I also require a design for a freestanding signboard that will be coordinated with the design of the office front please see the images attached labelled signboard.

Deliverable number 1:
I am looking for a minimalist contemporary design with strong colours to draw the attention of the passing Traffic.

The office facade is to be repainted so you may choose to recolour the office in any way to coordinate with logo however the attached logo must remain as is. I prefer the colours red black and white or shades of these colours.

Velko property managers is a new company looking to target property investors in the local area. Most of our clients are from a middle to upper income demographic. We help these investors to rent out their properties and ensure they are maintained in good condition and provide a regular income.

The area we operate in is centrally located and close to the central business district of Perth.

Our office is situated in a residential area on a busy road facing diagonally at 45° down the road. People see our office from their cars whilst driving to work, there is no pedestrian traffic in the area. Therefore the office façade needs to stand out and any signage must be read by quickly passing traffic or convey our brand in seconds. Whilst the view of the office from the road is obscured somewhat by trees from a distance, once within 50 to 100 m of the office the full face of the office front is visible facing directly at the driver.

No measurements are provided for the façade of the office (please see the photo provided), this is a blank canvas as the whole building will be repainted to fit in with YOUR design. A logo is also attached. The colours red black and white are preferred.

Please provide an image of the office with signage/colours superimposed.

Deliverable number 2:
Also attached is an image of a freestanding sign for which I require a design. This sign is used for advertising properties for lease or sale which will be erected outside the front of residential houses. Again this sign needs to be bold and bright with a contemporary design. It needs to stand out from the crowd of many other signs in the area, whilst the sign advertises the property it must also promote our company brand by having a prominent logo. The size of these signboards will either be 1250 mm x 900 mm or 1800 mm x 625 mm. Please note that this sign must be rectangular in shape and cannot have any text or logo protruding outside of the lines of the rectangular sign due to cost restrictions.

Target Market(s)

Industry/Entity Type

Real Estate

Font styles to use
Sans Serif

Colors
ec1f27
ffffff
000000

Requirements
Must have
• Contemporary uncluttered design using the colours red black and white of shades of.
Nice to have
• A prominent logo with the words "Property Managers" easily read by passing traffic.
• Files provided with editable text and the name of the font used.
Should not have
• designs protruding outside of the overall building facia or sign rectangle.

```html
<!DOCTYPE html>
<html lang="en">
<head>
<meta charset="utf-8">
<title>Velko Property Managers – For Lease or Sale Signboard</title>
<link rel="stylesheet" href="https://fonts.googleapis.com/css2?family=Gelasio:wght@700&family=Cabin:wght@400&display=swap">
<style>
  :root {
    --brand-red: #ec1f27;
    --shadow-red: #8e1218;
    --panel-mist: #e6f4f5;
    --ink: #2d3a40;
    --white: #ffffff;
  }
  * { margin: 0; padding: 0; box-sizing: border-box; }
  html, body { width: 1200px; height: 900px; overflow: hidden; background: var(--brand-red); }
  .signboard { position: relative; width: 1200px; height: 900px; background: var(--brand-red); }
  .headline {
    position: absolute; left: 0; top: 0; width: 1200px; height: 580px;
    font-family: "Gelasio", Georgia, serif; font-weight: 700; color: var(--white);
    text-shadow: 5px 5px 4px var(--shadow-red);
  }
  .headline-line { position: absolute; left: 0; width: 100%; text-align: center; font-size: 180px; line-height: 1; letter-spacing: -3px; white-space: nowrap; }
  .headline-line--first { top: 110px; left: 2px; }
  .headline-line--second { top: 358px; left: 29px; }
  .contact-band {
    position: absolute; left: 0; top: 582px; width: 1200px; height: 270px;
    background: var(--panel-mist);
    font-family: "Cabin", "Trebuchet MS", sans-serif; color: var(--ink);
  }
  .brand { position: absolute; left: 40px; top: 40px; width: 292px; text-align: center; }
  .brand-mark { display: block; width: 82px; height: 82px; margin: 0 auto 28px; background: var(--brand-red); border-radius: 6px; }
  .brand-name { display: block; font-size: 52px; line-height: 1; letter-spacing: 16px; text-transform: uppercase; padding-left: 16px; }
  .brand-tagline { display: block; margin-top: 12px; font-size: 16px; letter-spacing: 3px; text-transform: uppercase; padding-left: 3px; }
  .contact-details { position: absolute; left: 463px; top: 42px; width: 640px; text-align: center; font-size: 50px; line-height: 69px; }
</style>
</head>
<body>
  <main class="signboard">
    <h1 class="headline">
      <span class="headline-line headline-line--first">For Lease</span>
      <span class="headline-line headline-line--second">or Sale</span>
    </h1>
    <section class="contact-band">
      <div class="brand">
        <span class="brand-mark"></span>
        <span class="brand-name">Velko</span>
        <span class="brand-tagline">Property Managers</span>
      </div>
      <div class="contact-details">
        <p class="contact-mobile">Mobile 0411 222 3333</p>
        <p class="contact-office">Office 9000 1234</p>
        <p class="contact-web">www.velkoproperty.com.au</p>
      </div>
    </section>
  </main>
</body>
</html>
```